Business Card For Halvenmoor Financial Consulting

Hi, I would like a business card designed. Bold, modern.
Please use the same design as the logo. I have also attached the website design to see the overall theme.
Wordmark Font
Color: Hex: #01AEF7

```html
<!DOCTYPE html>
<html lang="en">
<head>
<meta charset="utf-8">
<title>Halvenmoor Financial Consulting – Business Card</title>
<link href="https://fonts.googleapis.com/css2?family=Montserrat:wght@500;700;800&family=Roboto:wght@400&display=swap" rel="stylesheet">
<style>
  :root {
    --backdrop: #7e7d7b;
    --paper: #fbfbfb;
    --navy: #13314f;
    --brand-blue: #01aef7;
    --ink: #3a3d42;
    --rule: #9aa7b4;
    --card-dark: #17222d;
    --pattern-light: #22313f;
  }
  * { box-sizing: border-box; margin: 0; padding: 0; }
  html, body { width: 1200px; height: 801px; overflow: hidden; }
  body {
    background: var(--backdrop);
    display: flex; align-items: center; justify-content: center; gap: 60px;
    font-family: "Roboto", Arial, sans-serif;
  }
  .card {
    width: 525px; height: 300px; position: relative;
    border-bottom: 3px solid var(--brand-blue);
    box-shadow: 0 10px 24px rgba(0,0,0,.25);
  }
  .card-front { background: var(--paper); display: flex; align-items: center; }
  .brand { width: 262px; display: flex; align-items: center; justify-content: center; gap: 12px; }
  .brand-square { width: 34px; height: 34px; border: 3px solid var(--brand-blue); flex: none; }
  .brand-name {
    font-family: "Montserrat", Arial, sans-serif; font-weight: 800;
    color: var(--navy); font-size: 22px; letter-spacing: 1px; line-height: 1;
  }
  .brand-sub {
    font-family: "Montserrat", Arial, sans-serif; font-weight: 800;
    color: var(--navy); font-size: 8.5px; letter-spacing: 4.6px; margin-top: 6px;
  }
  .divider { width: 1px; height: 170px; background: var(--rule); }
  .details { padding-left: 20px; color: var(--ink); font-size: 12px; line-height: 1.45; }
  .person-name {
    font-family: "Montserrat", Arial, sans-serif; font-weight: 800;
    color: var(--navy); font-size: 17px; letter-spacing: .3px;
  }
  .person-title { color: var(--brand-blue); font-size: 13px; margin-bottom: 12px; }
  .address { margin-bottom: 10px; }
  .contact-row { display: flex; align-items: center; gap: 7px; }
  .contact-row svg { width: 10px; height: 10px; fill: var(--brand-blue); flex: none; }
  .card-back { background: var(--card-dark); overflow: hidden; }
  .back-pattern {
    position: absolute; inset: 0;
    background: linear-gradient(120deg, var(--pattern-light) 0%, var(--card-dark) 55%, #141d26 100%);
  }
  .back-mark {
    position: absolute; right: 110px; top: 100px;
    display: flex; flex-direction: column; align-items: center; gap: 10px;
  }
  .back-square { width: 60px; height: 60px; border: 4px solid var(--brand-blue); }
  .back-name {
    font-family: "Montserrat", Arial, sans-serif; font-weight: 800;
    color: var(--brand-blue); font-size: 11px; letter-spacing: 1px;
  }
</style>
</head>
<body>
  <section class="card card-front">
    <div class="brand">
      <div class="brand-square"></div>
      <div>
        <div class="brand-name">HALVENMOOR</div>
        <div class="brand-sub">CONSULTING</div>
      </div>
    </div>
    <div class="divider"></div>
    <div class="details">
      <div class="person-name">MARLEN OSTRAVA</div>
      <div class="person-title">President</div>
      <div class="address">1480 Seabright Lane<br>Coral Bay CA 92651</div>
      <div class="contact-row">
        <svg viewBox="0 0 24 24" aria-hidden="true"><path d="M6.6 10.8a15 15 0 0 0 6.6 6.6l2.2-2.2c.3-.3.7-.4 1-.2 1.1.4 2.3.6 3.6.6.6 0 1 .4 1 1V20c0 .6-.4 1-1 1A17 17 0 0 1 3 4c0-.6.4-1 1-1h3.5c.6 0 1 .4 1 1 0 1.3.2 2.5.6 3.6.1.3 0 .7-.2 1z"/></svg>
        <span>555-014-2290</span>
      </div>
      <div class="contact-row">
        <svg viewBox="0 0 24 24" aria-hidden="true"><path d="M2 5h20v14H2zm2 2v.5l8 5 8-5V7l-8 5z"/></svg>
        <span>info@HalvenmoorConsulting.com</span>
      </div>
      <div class="contact-row">
        <svg viewBox="0 0 24 24" aria-hidden="true"><circle cx="12" cy="12" r="10"/></svg>
        <span>www.HalvenmoorConsulting.com</span>
      </div>
    </div>
  </section>

  <section class="card card-back">
    <div class="back-pattern" role="img" aria-label="Dark navy embossed repeating brand pattern"></div>
    <div class="back-mark">
      <div class="back-square"></div>
      <div class="back-name">HALVENMOOR</div>
    </div>
  </section>
</body>
</html>
```